Label Design for 2x Chutney Products

We need a label design for 2x Chutney Products.
Marigo Chutney - Red Chili
Marigo Chutney - Green Chili & Coriander
See attached pictures. This is just sample pictures so you get an impression of the product and the colors. Both labels to have as title the generic name "Marigo Chutney" and then added either Red Chili or Green Chili & Coriander. The different terms needs to be good readable and can differ in font/color/size, or in the same style if this makes more sense from design point (as I am not a designer). The labels later on need to be editable in the way that the ingredient list, nutrition list, basis company and production information can be added. If this needs to be done directly and cannot be edited later on please let know. Editable design related the additional text also would be good as the additional information need to be added in different languages (Dutch. German and perhaps French). No clue how this is to be implemented but looking forward to receive some input/solutions on this.
I already had a project to create the company logo. I consider this logo to be used as the product logo and not the company logo. A different company logo later on can be designed from new. This logo is here attached. Either to work with this logo and use it as product logo (perhaps revise the colors) and add the product description or create a new logo for the product from scratch if you feel too. The logo itself should be easily readable for the product name/description and the colors appealing to such product and of course customers.
Please contact if any clarification needed. Thanks in advance for your efforts and ideas for this project.

Industry/Entity Type

Food

Font styles to use
Other font styles liked:
• Asian Touch

Requirements
Nice to have
• If possible "simply" editable for text fields in order to add/revise the ingredient list, nutrition list, revise to different languages.

```html
<!DOCTYPE html>
<html lang="en">
<head>
<meta charset="utf-8">
<title>Marigo Chutney – Green Chili Label</title>
<link rel="stylesheet" href="https://fonts.googleapis.com/css2?family=Titan+One&family=Ubuntu:wght@500;700&display=swap">
<style>
  :root {
    --label-green: #196b05;
    --plate-green: #1a6a06;
    --lime: #6fe117;
    --chili-yellow: #fff200;
    --ink: #0b0b0b;
    --white: #ffffff;
    --silver-light: #f2f4f4;
    --silver-mid: #b9c1c1;
    --silver-dark: #6f7a7b;
    --outline-grey: #c8cccc;
    --brand-text: #1e1e1e;
  }
  html, body {
    margin: 0;
    padding: 0;
    width: 1200px;
    height: 480px;
    overflow: hidden;
    background: var(--white);
  }
  .label {
    position: relative;
    width: 1200px;
    height: 480px;
    background: var(--label-green);
    overflow: hidden;
  }
  .foil-band {
    position: absolute;
    left: 0;
    width: 1200px;
    height: 19px;
    background: linear-gradient(90deg, var(--silver-light) 0%, var(--silver-mid) 18%, var(--silver-light) 30%, var(--silver-dark) 56%, var(--silver-light) 72%, var(--silver-mid) 88%, var(--silver-light) 100%);
  }
  .foil-band--top { top: 0; box-shadow: 0 2px 3px rgba(0,0,0,.35); }
  .foil-band--bottom { bottom: 0; box-shadow: 0 -2px 3px rgba(0,0,0,.35); }

  .brand-tab {
    position: absolute;
    left: 557px;
    top: 19px;
    width: 86px;
    height: 135px;
    background: var(--white);
    border-radius: 0 0 20px 20px;
    display: flex;
    flex-direction: column;
    align-items: center;
  }
  .brand-tab__dot {
    width: 62px;
    height: 62px;
    margin-top: 19px;
    border-radius: 50%;
    background: var(--lime);
  }
  .brand-tab__name {
    margin-top: 10px;
    font-family: "Ubuntu", sans-serif;
    font-weight: 700;
    font-size: 12px;
    line-height: 13px;
    letter-spacing: 0.3px;
    text-align: center;
    color: var(--brand-text);
    text-transform: uppercase;
  }

  .product-title {
    position: absolute;
    left: 360px;
    top: 140px;
    width: 460px;
    height: 215px;
    overflow: visible;
  }
  .product-title text {
    font-family: "Titan One", sans-serif;
    paint-order: stroke fill;
    stroke-linejoin: round;
  }
  .variant-name {
    position: absolute;
    left: 522px;
    top: 342px;
    margin: 0;
    white-space: nowrap;
    font-family: "Ubuntu", sans-serif;
    font-weight: 500;
    font-size: 46px;
    line-height: 50px;
    color: var(--white);
  }

  .photo {
    position: absolute;
  }
  .photo--red-chilies {
    left: 189px;
    top: 282px;
    width: 292px;
    height: 146px;
    background: radial-gradient(ellipse at 50% 55%, #d81a10 0%, rgba(200,20,10,.75) 35%, rgba(25,107,5,0) 70%);
  }
  .photo--green-chilies {
    left: 872px;
    top: 19px;
    width: 300px;
    height: 442px;
    background:
      radial-gradient(ellipse 28% 30% at 26% 18%, rgba(92,190,48,.9) 0%, rgba(25,107,5,0) 100%),
      radial-gradient(ellipse 30% 38% at 75% 50%, rgba(52,150,30,.95) 0%, rgba(25,107,5,0) 100%),
      radial-gradient(ellipse 22% 32% at 32% 84%, rgba(92,190,48,.9) 0%, rgba(25,107,5,0) 100%);
  }
</style>
</head>
<body>
<main class="label">
  <div class="foil-band foil-band--top"></div>

  <div class="brand-tab">
    <div class="brand-tab__dot"></div>
    <div class="brand-tab__name">Sunvale<br>Foods</div>
  </div>

  <div class="photo photo--red-chilies" role="img" aria-label="Photo of two crossed red chili peppers"></div>
  <div class="photo photo--green-chilies" role="img" aria-label="Photo of three fresh green chili peppers"></div>

  <svg class="product-title" viewBox="360 140 460 215" role="heading" aria-level="1" aria-label="Marigo Chutney">
    <polygon class="product-title__plate"
      points="372,186 505,169 504,175 744,154 713,232 808,224 766,333 447,350 443,296 414,280 421,258 410,212"
      fill="var(--plate-green)" stroke="var(--outline-grey)" stroke-width="3" stroke-linejoin="round"/>
    <g transform="rotate(-3 590 250)">
      <text x="420" y="240" font-size="80" textLength="296" lengthAdjust="spacingAndGlyphs"
        fill="var(--lime)" stroke="var(--white)" stroke-width="9">Marigo</text>
      <text x="462" y="322" font-size="90" textLength="318" lengthAdjust="spacingAndGlyphs"
        fill="var(--ink)" stroke="var(--outline-grey)" stroke-width="22">Chutney</text>
      <text x="462" y="322" font-size="90" textLength="318" lengthAdjust="spacingAndGlyphs"
        fill="var(--ink)" stroke="var(--chili-yellow)" stroke-width="10">Chutney</text>
    </g>
  </svg>

  <p class="variant-name">Green Chili</p>

  <div class="foil-band foil-band--bottom"></div>
</main>
</body>
</html>
```